I need a website, primarily a landing page, for my company, Morrow Vantage. A sales training and cons

I need a web design/landing page for a new sales training and consulting company, morrow vantage. We perform "sales experiments" aimed at each individual or team, where we assist in helping them identify their strengths, through a series of "sales experiments" that we can tailor based on the individual and what they're trying to accomplish.

```html
<!DOCTYPE html>
<html lang="en">
<head>
<meta charset="utf-8">
<title>Morrow Vantage – Sales Training &amp; Consulting</title>
<link rel="stylesheet" href="https://fonts.googleapis.com/css2?family=Lato:wght@400;700;900&family=Open+Sans:wght@400;600&display=swap">
<style>
:root{
  --blue:#1f5c9c;
  --blue-dark:#184a80;
  --ink:#1e1e1e;
  --text:#555;
  --muted:#777;
  --line:#9a9a9a;
  --ring:#d9d9d9;
  --white:#fff;
}
*{box-sizing:border-box;margin:0;padding:0}
html,body{width:1200px;height:3564px;overflow:hidden;background:var(--white)}
body{position:relative;font-family:"Open Sans",Arial,sans-serif;color:var(--text)}

/* header */
.site-header{position:absolute;left:0;top:0;width:1200px;height:110px;background:var(--white);z-index:3}
.top-contact{position:absolute;right:110px;top:20px;font-size:15px;color:#333;display:flex;align-items:center;gap:10px}
.top-contact svg{width:14px;height:14px;fill:var(--blue)}
.top-contact .sep{color:#999}
.main-nav{position:absolute;right:110px;top:66px;display:flex;gap:34px;align-items:center;font-family:Lato,sans-serif;font-weight:700;font-size:16px;color:#333;text-transform:uppercase}
.main-nav .active{color:var(--blue)}
.main-nav svg{width:16px;height:16px}
.brand{position:absolute;left:106px;top:-4px;width:268px;height:268px;border-radius:50%;background:var(--white);z-index:4;display:flex;flex-direction:column;align-items:center;justify-content:flex-end;padding-bottom:84px}
.brand-dot{width:26px;height:26px;border-radius:50%;border:3px solid var(--blue);margin-bottom:14px}
.brand-name{font-family:Lato,sans-serif;font-weight:900;font-size:24px;color:var(--blue);text-transform:uppercase;white-space:nowrap}

/* hero */
.hero{position:absolute;left:0;top:110px;width:1200px;height:630px;overflow:hidden}
.hero-photo{position:absolute;inset:0;background:radial-gradient(ellipse at 50% 45%,#f2b66a 0%,#c98a4c 18%,#7a6a5e 45%,#46464a 75%,#2e3034 100%)}
.hero-title{position:absolute;left:0;width:1200px;top:210px;text-align:center;font-family:Lato,sans-serif;font-weight:700;font-size:47px;line-height:68px;color:var(--white)}
.hero-btn{position:absolute;left:458px;top:386px;width:285px;height:62px;border:2px solid var(--white);border-radius:31px;color:var(--white);font-family:Lato,sans-serif;font-weight:700;font-size:16px;letter-spacing:.5px;display:flex;align-items:center;justify-content:center}
.hero-dots{position:absolute;left:571px;top:558px;display:flex;gap:4px}
.hero-dots span{width:11px;height:11px;border-radius:50%;border:2px solid var(--white)}
.hero-dots span:first-child{background:var(--white)}

/* welcome */
.welcome-mark{position:absolute;left:751px;top:794px;width:26px;height:26px;border-radius:50%;border:3px solid var(--blue)}
.section-title{position:absolute;left:0;width:1200px;text-align:center;font-family:Lato,sans-serif;font-weight:700;font-size:40px;line-height:46px;color:var(--ink);text-transform:uppercase}
.welcome-copy{position:absolute;left:230px;width:740px;top:898px;text-align:center;font-size:14.5px;line-height:30px;color:var(--text)}
.video{position:absolute;left:400px;top:1031px;width:403px;height:266px;background:linear-gradient(135deg,#2c3a4a,#5f7388 50%,#cfd6dc);box-shadow:0 6px 14px rgba(0,0,0,.35)}
.video-play{position:absolute;left:174px;top:105px;width:56px;height:56px;border-radius:50%;background:#111;display:flex;align-items:center;justify-content:center}

/* experiments */
.experiments{position:absolute;left:0;top:1418px;width:1200px;height:602px;overflow:hidden;background:#1f1f22}
.experiments-photo{position:absolute;left:0;top:0;width:760px;height:602px;background:linear-gradient(120deg,#d8e1ea 0%,#9fb3c6 35%,#c98a3c 70%,#3a2a1c 100%)}
.experiments-circle{position:absolute;left:574px;top:-300px;width:920px;height:866px;border-radius:50%;background:var(--white)}
.experiments-content{position:absolute;left:676px;width:440px;top:0;height:602px;text-align:center}
.experiments-content svg{position:absolute;left:192px;top:70px}
.experiments-content h2{position:absolute;left:0;width:440px;top:152px;font-family:Lato,sans-serif;font-weight:700;font-size:40px;line-height:46px;color:var(--ink)}
.experiments-content p{position:absolute;left:20px;width:400px;top:222px;font-size:14px;line-height:29px;color:var(--text)}
.btn-solid{position:absolute;background:var(--blue);color:var(--white);border-radius:30px;font-family:Lato,sans-serif;font-weight:700;font-size:15px;display:flex;align-items:center;justify-content:center}

/* services */
.service{position:absolute;width:240px;text-align:center}
.service-icon{position:relative;width:166px;height:166px;margin:0 auto;border-radius:50%;border:10px solid var(--ring);display:flex;align-items:center;justify-content:center}
.service h3{margin-top:18px;font-family:Lato,sans-serif;font-weight:700;font-size:24px;color:var(--ink)}
.service p{margin:14px auto 0;width:212px;font-size:13.5px;line-height:24px;color:var(--text)}

/* contact */
.contact{position:absolute;left:0;top:2645px;width:1200px;height:567px;overflow:hidden}
.contact-photo{position:absolute;left:618px;top:0;width:582px;height:567px;background:linear-gradient(135deg,#dcd6cf 0%,#a89484 40%,#6b5546 65%,#2d2a2c 100%)}
.contact-circle{position:absolute;left:-40px;top:-150px;width:700px;height:682px;border-radius:50%;background:var(--white)}
.contact h2{position:absolute;left:112px;top:60px;font-family:Lato,sans-serif;font-weight:700;font-size:40px;line-height:46px;color:var(--ink)}
.field{position:absolute;border:1.5px solid #888;background:var(--white);font-size:14px;color:#444;padding:10px 14px}

/* footer */
.socials{position:absolute;top:3319px;left:489px;display:flex;gap:9px}
.socials span{width:48px;height:48px;border-radius:50%;border:1.5px solid #888}
.footer-line{position:absolute;left:0;width:1200px;text-align:center;font-size:14px;color:#444}
.footer-line svg{width:12px;height:12px;fill:var(--blue);vertical-align:-1px;margin-right:4px}
.footer-line .sep{margin:0 10px}
</style>
</head>
<body>

<header class="site-header">
  <div class="top-contact">
    <svg viewBox="0 0 24 24"><path d="M6.6 10.8a15 15 0 0 0 6.6 6.6l2.2-2.2a1 1 0 0 1 1-.25 11.4 11.4 0 0 0 3.6.57 1 1 0 0 1 1 1V20a1 1 0 0 1-1 1A17 17 0 0 1 3 4a1 1 0 0 1 1-1h3.5a1 1 0 0 1 1 1c0 1.25.2 2.45.57 3.57a1 1 0 0 1-.25 1z"/></svg>
    <span>1 800 555 0142</span><span class="sep">|</span>
    <svg viewBox="0 0 24 24"><path d="M2 5h20v14H2zm2 2v.5l8 5 8-5V7z"/></svg>
    <span>info@morrowvantage.com</span>
  </div>
  <nav class="main-nav">
    <span class="active">Home</span><span>About Us</span><span>What We Do</span><span>News &amp; Insights</span><span>Contact</span>
    <svg viewBox="0 0 24 24" fill="none" stroke="#333" stroke-width="3"><circle cx="10" cy="10" r="6"/><path d="M15 15l6 6"/></svg>
  </nav>
</header>

<div class="brand">
  <div class="brand-dot"></div>
  <div class="brand-name">Morrow Vantage</div>
</div>

<section class="hero">
  <div class="hero-photo" role="img" aria-label="Misty mountain peaks glowing in a golden sunrise"></div>
  <h1 class="hero-title">Optimize performance in Business and in Life.<br>Success. It's in your DNA.</h1>
  <div class="hero-btn">REQUEST A CONSULTATION</div>
  <div class="hero-dots"><span></span><span></span><span></span><span></span></div>
</section>

<div class="welcome-mark"></div>
<h2 class="section-title" style="top:826px">Welcome to Morrow Vantage</h2>
<p class="welcome-copy">Nemo enim ipsam voluptatem quia voluptas sit aspernatur aut odit aut fugit, sed quia consequuntur magni dolores eos qui ratione voluptatem sequi nesciunt. Neque porro quisquam est, qui dolorem ipsum quia dolor sit amet, consectetur, adipisci velit, sed quia non numquam eius modi tempora.</p>
<div class="video" role="img" aria-label="Video still of a hand touching a glowing digital interface">
  <div class="video-play"><svg width="22" height="24" viewBox="0 0 22 24"><path d="M4 2l16 10L4 22z" fill="#fff"/></svg></div>
</div>

<section class="experiments">
  <div class="experiments-photo" role="img" aria-label="Hand with a pen reviewing colourful sales charts on paper"></div>
  <div class="experiments-circle"></div>
  <div class="experiments-content">
    <svg width="56" height="44" viewBox="0 0 56 44" fill="var(--blue)"><rect x="4" y="22" width="7" height="16"/><rect x="15" y="12" width="7" height="26"/><rect x="26" y="18" width="7" height="20"/><rect x="37" y="6" width="7" height="32"/><rect x="0" y="40" width="54" height="3"/></svg>
    <h2>SALES EXPERIMENTS</h2>
    <p>Sed ut perspiciatis unde omnis iste natus error sit vo luptatem accusantium doloremque laudantium, totam rem aperiam, eaque ipsa quae ab illo inventore veritatis et qua si architecto beatae vitae numquam.</p>
  </div>
  <div class="btn-solid" style="left:775px;top:376px;width:245px;height:59px">OUR SALES PERSPECTIVE</div>
</section>

<h2 class="section-title" style="top:2118px">What We Do</h2>

<div class="service" style="left:96px;top:2227px">
  <div class="service-icon"><svg width="64" height="56" viewBox="0 0 64 56"><ellipse cx="30" cy="24" rx="24" ry="18" fill="none" stroke="var(--blue)" stroke-width="5"/><path d="M14 38l-6 12 16-8" fill="var(--blue)"/><ellipse cx="30" cy="24" rx="14" ry="9" fill="var(--blue)" opacity=".25"/></svg></div>
  <h3>Consulting</h3>
  <p>Nemo enim ipsam voluptatem quia voluptas sit aspernatur aodit aut fugit, sed quia con.</p>
</div>
<div class="service" style="left:350px;top:2227px">
  <div class="service-icon"><svg width="70" height="64" viewBox="0 0 70 64" fill="var(--blue)"><circle cx="26" cy="26" r="16"/><g stroke="var(--blue)" stroke-width="7"><path d="M26 4v44M4 26h44M10 10l32 32M42 10L10 42"/></g><circle cx="26" cy="26" r="6" fill="#fff"/><circle cx="52" cy="46" r="10"/><g stroke="var(--blue)" stroke-width="5"><path d="M52 32v28M38 46h28"/></g><circle cx="52" cy="46" r="4" fill="#fff"/></svg></div>
  <h3>Sales Training</h3>
  <p>Nemo enim ipsam voluptatem quia voluptas sit aspernatur aodit aut fugit, sed quia con.</p>
</div>
<div class="service" style="left:605px;top:2227px">
  <div class="service-icon"><svg width="70" height="60" viewBox="0 0 70 60" fill="none" stroke="var(--blue)" stroke-width="5"><path d="M4 4v52h62"/><path d="M12 46l16-18 12 10 20-24"/><path d="M50 12h12v12"/></svg></div>
  <h3>Coaching</h3>
  <p>Nemo enim ipsam voluptatem quia voluptas sit aspernatur aodit aut fugit, sed quia con.</p>
</div>
<div class="service" style="left:857px;top:2227px">
  <div class="service-icon"><svg width="56" height="56" viewBox="0 0 56 56" fill="var(--blue)"><path d="M28 2l6 8 10-3 1 10 10 4-5 9 5 9-10 4-1 10-10-3-6 8-6-8-10 3-1-10-10-4 5-9-5-9 10-4 1-10 10 3z"/></svg></div>
  <h3>Sales Qualifications</h3>
  <p>Nemo enim ipsam voluptatem quia voluptas sit aspernatur aodit aut fugit, sed quia con.</p>
</div>

<section class="contact">
  <div class="contact-photo" role="img" aria-label="Two business people shaking hands"></div>
  <div class="contact-circle"></div>
  <h2>GET IN TOUCH</h2>
  <div class="field" style="left:112px;top:140px;width:224px;height:42px">First Name</div>
  <div class="field" style="left:347px;top:140px;width:226px;height:42px">Last Name</div>
  <div class="field" style="left:112px;top:194px;width:224px;height:43px">Email Address</div>
  <div class="field" style="left:347px;top:194px;width:226px;height:43px">Phone Number</div>
  <div class="field" style="left:112px;top:247px;width:461px;height:83px">Message</div>
  <div class="btn-solid" style="left:112px;top:363px;width:145px;height:48px">CONTACT US</div>
</section>

<div class="socials" aria-label="Social media links"><span></span><span></span><span></span><span></span></div>
<p class="footer-line" style="top:3407px">
  <svg viewBox="0 0 24 24"><path d="M12 2a7 7 0 0 0-7 7c0 5 7 13 7 13s7-8 7-13a7 7 0 0 0-7-7zm0 9.5A2.5 2.5 0 1 1 12 6.5a2.5 2.5 0 0 1 0 5z"/></svg>48 Harbour Lane, Eastfield, K2P 1L6<span class="sep">|</span><svg viewBox="0 0 24 24"><path d="M6.6 10.8a15 15 0 0 0 6.6 6.6l2.2-2.2a1 1 0 0 1 1-.25 11.4 11.4 0 0 0 3.6.57 1 1 0 0 1 1 1V20a1 1 0 0 1-1 1A17 17 0 0 1 3 4a1 1 0 0 1 1-1h3.5a1 1 0 0 1 1 1c0 1.25.2 2.45.57 3.57a1 1 0 0 1-.25 1z"/></svg>1 800 555 0142<span class="sep">|</span><svg viewBox="0 0 24 24"><path d="M2 5h20v14H2zm2 2v.5l8 5 8-5V7z"/></svg>info@morrowvantage.com
</p>
<p class="footer-line" style="top:3445px">Help<span class="sep">|</span>FAQ<span class="sep">|</span>Support<span class="sep">|</span>Sitemap<span class="sep">|</span>Terms Of Use<span class="sep">|</span>Privacy Statement</p>
<p class="footer-line" style="top:3483px">Morrow Vantage © 2018 All rights reserved.</p>

</body>
</html>
```